Advanced Therapeutic Massage Therapist

I need a business card advertising my massage services as an advanced therapeutic massage therapist. I offer advanced therapeutic massage, swedish and deep tissue. I want to create a simple, professional and feminine card. I like bright colours and creativity.

I prefer a bold and experimental approach rather than something status-quo. A card to suggest therapeutic healing through dynamic massage. Motifs, shapes or layout which suggest movement and flow.
Updates

Target Market(s)

Everybody!

Industry/Entity Type

Health And Wellness

Contact Information for Business Card

The card should include:
My name, logo, services offered and my contact details.

Sláine Dunleavy
Massage Therapist

- Swedish - Deep Tissue - Advanced Therapeutic

Phone: (+353) 87 216 4093
Email: regenerate@slainedunleavy-example.com
Website: www.slainedunlevy-example.com

Font styles to use
Serif
Sans Serif
Decorative
Script

Colors

Designer to choose colors to be used in the design.

Requirements
Must have
• An example may contain something like this, yet concise:
• "Sláine Dunleavy
• Massage Therapist
• - Swedish - Deep Tissue - Advanced Therapeutic"
Nice to have
• This sentence is optional:
• Imagery such as a logo or symbol. I have attached a file containing a logo I had produced however the name is incorrect now as it is "Sláine" not "Nelly". It could be edited to change it to Sláine.
• I have sent the file as .psd .jpg. .pdf and .png
• I like when the card conveys energy, movement, pressure points, flow etc.
• I just like the designer to follow their own style and ideas. I like bright colours but must have a lot of a base colour to offset it. I really prefer them to follow their own inspiration. That is my preference.
Should not have
• Pine trees, non-native trees to Britain and Ireland, exotic flowers or animals that are not native to Britain and Ireland.
• I don't like brown as the background colour of the card.
• The cars shouldn't look like a wedding invitation i.e too many floral type designs.

```html
<!DOCTYPE html>
<html lang="en">
<head>
<meta charset="utf-8">
<title>Sláine Dunleavy – Massage Therapist Business Card</title>
<link rel="stylesheet" href="https://fonts.googleapis.com/css2?family=Crimson+Text:ital,wght@0,400;0,600;1,400;1,600&family=Pinyon+Script&display=swap">
<style>
  :root {
    --stage: #231f20;
    --paper: #fdfcfa;
    --pattern-warm: #f3e6dc;
    --teal: #5cc0a5;
    --teal-deep: #3f8f82;
    --teal-glow: #6fc4b0;
    --ink: #3a3433;
    --accent-brown: #8a5a3c;
    --rule: #c9a892;
    --white: #ffffff;
  }
  * { margin: 0; padding: 0; box-sizing: border-box; }
  html, body { width: 1200px; height: 1200px; overflow: hidden; }
  body {
    background: var(--stage);
    font-family: "Crimson Text", Georgia, serif;
    color: var(--ink);
    position: relative;
  }
  .card-panel {
    position: absolute;
    left: 150px;
    width: 900px;
    height: 515px;
    overflow: hidden;
  }
  .card-inside { top: 70px; background: var(--paper); }
  .card-outside { top: 615px; }

  .pattern-field { position: absolute; inset: 0; }
  .inside-pattern {
    background: radial-gradient(ellipse at 55% 40%, var(--pattern-warm) 0%, rgba(243,230,220,0.35) 55%, var(--paper) 100%);
  }

  .brand-block {
    position: absolute;
    left: 70px; top: 80px;
    width: 290px;
    text-align: center;
  }
  .brand-mark {
    width: 170px; height: 170px;
    border-radius: 50%;
    background: var(--teal-glow);
    margin: 0 auto 18px;
  }
  .brand-name {
    font-size: 34px;
    font-weight: 400;
    color: var(--ink);
    line-height: 1;
  }
  .brand-role {
    font-size: 18px;
    color: var(--ink);
    margin-top: 6px;
    letter-spacing: 0.5px;
  }

  .divider {
    position: absolute;
    left: 395px; top: 55px;
    width: 1px; height: 300px;
    background: var(--rule);
  }

  .details-block { position: absolute; left: 430px; top: 70px; }
  .service-list { list-style: none; margin-bottom: 30px; }
  .service-list li {
    font-size: 27px;
    line-height: 1.25;
    display: flex; align-items: center; gap: 12px;
  }
  .service-list li::before {
    content: "★";
    color: var(--accent-brown);
    font-size: 16px;
  }
  .contact-list { list-style: none; }
  .contact-list li {
    font-size: 27px;
    line-height: 1.3;
    display: flex; align-items: center; gap: 12px;
  }
  .contact-icon { width: 16px; height: 16px; flex: none; }

  .tagline-band {
    position: absolute;
    left: 0; right: 0; bottom: 0;
    height: 98px;
    background: var(--paper);
  }
  .tagline-band::before {
    content: "";
    position: absolute;
    left: 0; right: 0; top: 0; height: 22px;
    background: var(--teal);
  }
  .tagline-band .tagline {
    position: absolute;
    left: 0; right: 0; top: 22px; bottom: 22px;
    background: var(--teal);
    border-top: 4px solid var(--paper);
    display: flex; align-items: center; justify-content: center;
    font-size: 26px; font-style: italic; font-weight: 600;
    color: var(--ink);
    white-space: nowrap;
  }

  .outside-pattern {
    background:
      radial-gradient(ellipse at 45% 40%, var(--teal-glow) 0%, #58a996 40%, var(--teal-deep) 100%);
  }
  .cover-title {
    position: absolute;
    left: 0; right: 0; top: 175px;
    text-align: center;
    color: var(--white);
  }
  .cover-name {
    font-family: "Pinyon Script", cursive;
    font-size: 86px;
    font-weight: 400;
    line-height: 1;
  }
  .cover-role {
    font-size: 46px;
    margin-top: 6px;
    letter-spacing: 1px;
  }
</style>
</head>
<body>

  <section class="card-panel card-inside">
    <div class="pattern-field inside-pattern" role="img" aria-label="Faint warm swirling leaf pattern across the card background"></div>

    <div class="brand-block">
      <div class="brand-mark"></div>
      <div class="brand-name">Nelly Dunleavy</div>
      <div class="brand-role">massage therapist</div>
    </div>

    <div class="divider"></div>

    <div class="details-block">
      <ul class="service-list">
        <li>Swedish</li>
        <li>Deep Tissue</li>
        <li>Advanced Therapeutic</li>
      </ul>
      <ul class="contact-list">
        <li>
          <svg class="contact-icon" viewBox="0 0 16 16" aria-hidden="true"><path d="M4 1h3l1 4-2 1a9 9 0 0 0 4 4l1-2 4 1v3c0 1-1 2-2 2A13 13 0 0 1 2 3c0-1 1-2 2-2z" fill="#8a5a3c"/></svg>
          (+353) 87 216 4093
        </li>
        <li>
          <svg class="contact-icon" viewBox="0 0 16 16" aria-hidden="true"><circle cx="8" cy="8" r="7" fill="none" stroke="#8a5a3c" stroke-width="1.6"/><ellipse cx="8" cy="8" rx="3" ry="7" fill="none" stroke="#8a5a3c" stroke-width="1.2"/><line x1="1" y1="8" x2="15" y2="8" stroke="#8a5a3c" stroke-width="1.2"/></svg>
          www.slainemassage-example.com
        </li>
        <li>
          <svg class="contact-icon" viewBox="0 0 16 16" aria-hidden="true"><rect x="1" y="3" width="14" height="10" fill="#8a5a3c"/></svg>
          slainemassage@example-mail.com
        </li>
      </ul>
    </div>

    <div class="tagline-band">
      <p class="tagline">Glenmara Board qualified specialising in advanced therapeutic and deep tissue massage</p>
    </div>
  </section>

  <section class="card-panel card-outside">
    <div class="pattern-field outside-pattern" role="img" aria-label="Teal background with a soft glowing centre and faint swirling tree and leaf pattern"></div>
    <div class="cover-title">
      <h1 class="cover-name">Sláine Dunleavy</h1>
      <p class="cover-role">Massage Therapist</p>
    </div>
  </section>

</body>
</html>
```